New business card/stationary for a consulting company

I am looking for a clean and very professional looking business card for my consulting company as well as corresponding stationary. I am uploading our logo. I like simple and powerful for the feel. No graphics but I am open on everything else. Below is my contact information but would like the final to be in a version I can add my employees information into and print. Thank you.

Daniel Whitcombe
dan@ferncliffadvisory.com
2870 North 9th Avenue, Summit Floor, Elm Ridge, Illinois 60531
www.ferncliffadvisory.com

Industry/Entity Type

Consulting

Contact Information for Business Card

Daniel Whitcombe
dan@ferncliffadvisory.com
www.ferncliffadvisory.com

Font styles to use
Serif
Sans Serif

Requirements
Must have
• Our logo and the business card details.
Nice to have
• our website www.ferncliffadvisory.com

```html
<!DOCTYPE html>
<html lang="en">
<head>
<meta charset="utf-8">
<title>Ferncliff Advisory — Business Card</title>
<link rel="stylesheet" href="https://fonts.googleapis.com/css2?family=Roboto:wght@300;400&display=swap">
<style>
  :root {
    --backdrop: #3b3b3d;
    --card: #232427;
    --card-edge: #1b1c1e;
    --gloss-text: #4d4e53;
    --brand-blue: #1f4f87;
    --name-blue: #2a6cb3;
    --ink-light: #f2f2f2;
  }
  * { box-sizing: border-box; margin: 0; padding: 0; }
  html, body {
    width: 799px; height: 1200px; overflow: hidden;
    background: var(--backdrop);
    font-family: "Roboto", Arial, sans-serif;
  }
  .sheet {
    width: 799px; height: 1200px;
    display: flex; flex-direction: column; align-items: center; justify-content: center;
    gap: 150px;
  }
  .card {
    position: relative;
    width: 600px; height: 343px;
    background: var(--card);
    border: 1px solid var(--card-edge);
    box-shadow: 0 18px 40px rgba(0,0,0,0.45);
  }

  /* front */
  .card-front { display: flex; align-items: center; justify-content: center; }
  .front-brand {
    display: flex; align-items: center; gap: 16px;
    white-space: nowrap;
  }
  .front-brand .brand-square { width: 20px; height: 20px; background: var(--gloss-text); }
  .front-brand .brand-name {
    font-size: 30px; font-weight: 400; letter-spacing: 4px; text-transform: uppercase;
    color: var(--gloss-text);
  }

  /* back */
  .brand {
    position: absolute; right: 34px; top: 92px;
    display: flex; align-items: center; gap: 12px;
    white-space: nowrap;
  }
  .brand .brand-square { width: 16px; height: 16px; background: var(--brand-blue); }
  .brand .brand-name {
    font-size: 22px; font-weight: 400; letter-spacing: 2px; text-transform: uppercase;
    color: var(--ink-light);
  }
  .contact {
    position: absolute; left: 34px; bottom: 42px;
    color: var(--ink-light); font-size: 14px;
    white-space: nowrap;
  }
  .contact-name {
    font-size: 20px; font-weight: 300; letter-spacing: 2px; text-transform: uppercase;
    color: var(--name-blue); margin-bottom: 10px;
  }
  .contact-line { display: flex; align-items: center; gap: 7px; margin-top: 6px; }
  .contact-line .gap { width: 14px; }
  .contact-line svg { width: 12px; height: 12px; fill: var(--name-blue); flex: none; }
</style>
</head>
<body>
  <main class="sheet">
    <section class="card card-front" aria-label="Card front">
      <div class="front-brand">
        <span class="brand-square"></span>
        <span class="brand-name">Ferncliff Advisory</span>
      </div>
    </section>

    <section class="card card-back" aria-label="Card back">
      <div class="brand">
        <span class="brand-square"></span>
        <span class="brand-name">Ferncliff Advisory</span>
      </div>
      <div class="contact">
        <p class="contact-name">Daniel Whitcombe</p>
        <p class="contact-line">
          <svg viewBox="0 0 12 12" aria-hidden="true"><path d="M0 2h12v8H0z"/></svg>
          dan@ferncliffadvisory.com
          <span class="gap"></span>
          <svg viewBox="0 0 12 12" aria-hidden="true"><circle cx="6" cy="6" r="6"/></svg>
          www.ferncliffadvisory.com
        </p>
        <p class="contact-line">
          <svg viewBox="0 0 12 12" aria-hidden="true"><path d="M6 0a4.5 4.5 0 0 1 4.5 4.5C10.5 8 6 12 6 12S1.5 8 1.5 4.5A4.5 4.5 0 0 1 6 0zm0 3a1.5 1.5 0 1 0 0 3 1.5 1.5 0 0 0 0-3z"/></svg>
          2870 North 9th Avenue, Summit Floor, Elm Ridge, Illinois 60531
        </p>
      </div>
    </section>
  </main>
</body>
</html>
```